Advertising company unique advertising platform

we need a logo design for a new company based in Australia Melbourne. We develop innovated advertising platform where consumer can use this platform to get regular discount, as business owner they can use this platform for free advertisement. Payment for this advertisement platform only payable every two weeks, when I generate revenue for their business

Industry/Entity Type

Advertising

Contact Information for Business Card

Dale Morven | Co-Founder |Managing Director
Suite 718 240 Wattlebrook Lane Melbourne Vic 3000

ABN 38 614 207 923
Tel: +61 0487 259 318 | Email: dale.morven@plivorantu.com

Font styles to use
Decorative
Script

Requirements
Must have
• Try few different design and some round corner business card
Should not have
• One round corner business card...try 4 different colour background not only black, make sure two side is designed. Be creative so imagine you are giving this to a client make sure has wow factor, if you can also try one design with engrave like all the logo, words look 3d feel
• The word Advertising Platform use attached file font

```html
<!DOCTYPE html>
<html lang="en">
<head>
<meta charset="utf-8">
<title>Plivorantu Business Card</title>
<link href="https://fonts.googleapis.com/css2?family=Roboto:wght@400;500;700&display=swap" rel="stylesheet">
<style>
  :root {
    --backdrop: #d9d4cf;
    --front-red: #e2432f;
    --front-orange: #f08a2c;
    --front-yellow: #f4cf4a;
    --front-teal: #4fd6c0;
    --front-blue: #3aa6e6;
    --front-periwinkle: #6e8fdc;
    --panel-white: #f7f7f5;
    --name-red: #e2452d;
    --title-blue: #5d8fd6;
    --back-dark: #1d1e20;
    --logo-teal: #2fd3b4;
    --logo-orange: #f0672c;
    --text-white: #ffffff;
  }
  * { margin: 0; padding: 0; box-sizing: border-box; }
  html, body { width: 1200px; height: 960px; overflow: hidden; }
  body {
    position: relative;
    background: var(--backdrop);
    font-family: "Roboto", Arial, sans-serif;
  }
  .card {
    position: absolute;
    width: 600px;
    height: 342px;
    border-radius: 22px;
    overflow: hidden;
  }
  .card-front {
    left: 314px;
    top: 113px;
    background:
      radial-gradient(ellipse 260px 200px at 170px 190px, var(--front-yellow) 0%, rgba(244,207,74,0) 100%),
      linear-gradient(90deg, var(--front-red) 0%, var(--front-orange) 40%, var(--front-orange) 58%, var(--front-teal) 72%, var(--front-periwinkle) 86%, var(--front-blue) 100%);
  }
  .card-back {
    left: 311px;
    top: 472px;
    background: var(--back-dark);
  }
  .contact-block {
    position: absolute;
    left: 35px;
    top: 108px;
    color: var(--text-white);
    font-size: 14.5px;
    line-height: 18px;
  }
  .contact-group { margin-bottom: 7px; }
  .contact-line { display: flex; align-items: center; gap: 8px; height: 20px; }
  .contact-line svg { width: 13px; height: 13px; fill: var(--text-white); flex: none; }
  .name-panel {
    position: absolute;
    left: 295px;
    top: 82px;
    width: 210px;
    height: 210px;
    border-radius: 50%;
    background: var(--panel-white);
  }
  .holder {
    position: absolute;
    left: 295px;
    top: 157px;
    width: 210px;
    text-align: center;
  }
  .holder-name {
    color: var(--name-red);
    font-size: 20px;
    font-weight: 500;
    letter-spacing: 0.2px;
    margin-bottom: 8px;
  }
  .holder-title {
    color: var(--title-blue);
    font-size: 15.5px;
    line-height: 19px;
  }
  .brand {
    position: absolute;
    left: 0;
    top: 150px;
    width: 600px;
    display: flex;
    justify-content: center;
    align-items: center;
    gap: 14px;
  }
  .brand-dot {
    width: 26px;
    height: 26px;
    border-radius: 50%;
    background: var(--logo-orange);
  }
  .brand-name {
    color: var(--logo-teal);
    font-size: 36px;
    font-weight: 500;
  }
  .website {
    position: absolute;
    left: 0;
    top: 294px;
    width: 600px;
    text-align: center;
    color: var(--text-white);
    font-size: 13px;
    letter-spacing: 4.2px;
  }
</style>
</head>
<body>
  <section class="card card-front">
    <div class="contact-block">
      <div class="contact-group">
        <div>Plivorantu</div>
        <div>ABN 38 614 207 923</div>
      </div>
      <div class="contact-group">
        <div>Suite 718 240 Wattlebrook Lane</div>
        <div>Melbourne Vic 3000</div>
      </div>
      <div class="contact-line">
        <svg viewBox="0 0 24 24" aria-hidden="true"><path d="M6.6 10.8a15.1 15.1 0 0 0 6.6 6.6l2.2-2.2c.3-.3.7-.4 1-.2 1.1.4 2.3.6 3.6.6.6 0 1 .4 1 1V20c0 .6-.4 1-1 1A17 17 0 0 1 3 4c0-.6.4-1 1-1h3.5c.6 0 1 .4 1 1 0 1.3.2 2.5.6 3.6.1.3 0 .7-.2 1z"/></svg>
        <span>+61 0487 259 318</span>
      </div>
      <div class="contact-line">
        <svg viewBox="0 0 24 24" aria-hidden="true"><path d="M2 5h20v14H2z" opacity="0"/><path d="M2 6l10 7 10-7V5H2zm0 2.4V19h20V8.4l-10 7z"/></svg>
        <span>dale.morven@plivorantu.com</span>
      </div>
    </div>
    <div class="name-panel"></div>
    <div class="holder">
      <div class="holder-name">DALE MORVEN</div>
      <div class="holder-title">CO-FOUNDER<br>MANAGING DIRECTOR</div>
    </div>
  </section>

  <section class="card card-back">
    <div class="brand">
      <span class="brand-dot"></span>
      <span class="brand-name">Nexora Loop</span>
    </div>
    <div class="website">www.plivorantu.com</div>
  </section>
</body>
</html>
```